Business Card Design Project

This is the first time we use our new logo. We need a business card that we can use both on our institutional corporate relationships and also that works for our staff that deals with consumers directly.

VELUNDA is a new company dedicated to empower consumers and to provide them with the best choices for specialized health care using the latest telemedicine technology (medicine at a distance via videoconference).

We want to print this cards in high quality materials and process. We will like designs that allow us to use UV spot varnish and other techniques that will differentiate us.

We are including Two different versions of Color logos. In addition we are including white over black background logos. Those can be used replacing the black for a color.

Please note this is the first time we will be creating any corporate materials with our new logo and colors.

Target Market(s)

34+ consumers of medium high and high socioeconomic levels.

Industry/Entity Type

Health

Requirements
Must have
• Our logo on its original colors
Should not have
• Any other graphical element or design that is not our logo

```html
<!DOCTYPE html>
<html lang="en">
<head>
<meta charset="utf-8">
<title>VELUNDA Business Card Set</title>
<link rel="stylesheet" href="https://fonts.googleapis.com/css2?family=Jost:wght@400;500;600;700&display=swap">
<style>
  :root {
    --stage: #ece8e3;
    --label: #1a1a1a;
    --navy: #1b5a87;
    --sky: #5ab8e3;
    --mark: #3a8fd0;
    --ink: #111111;
    --muted: #444444;
    --white: #ffffff;
    --silver-light: #eeeeee;
    --silver-mid: #c9c9c9;
    --steel-dark: #2b2b2b;
  }
  * { box-sizing: border-box; margin: 0; padding: 0; }
  html, body { width: 1200px; height: 788px; overflow: hidden; }
  body {
    background: var(--stage);
    font-family: "Jost", "Futura", sans-serif;
    position: relative;
  }
  .card-label {
    position: absolute;
    width: 300px;
    text-align: center;
    font-size: 20px;
    color: var(--label);
  }
  .card {
    position: absolute;
    width: 527px;
    height: 300px;
    border-radius: 22px;
    overflow: hidden;
    box-shadow: 0 4px 12px rgba(0,0,0,0.25);
  }
  .card--front { left: 53px; top: 73px;
    background: linear-gradient(180deg, var(--silver-light), var(--silver-mid) 60%, #e2e2e2); }
  .card--white { left: 622px; top: 73px; background: var(--white); }
  .card--steel { left: 53px; top: 445px;
    background: linear-gradient(175deg, #f3f3f3 0%, #bdbdbd 40%, #6a6a6a 75%, var(--steel-dark) 100%); }
  .card--navy { left: 622px; top: 445px; background: var(--navy); }

  .brand { position: absolute; display: flex; align-items: center; gap: 16px; }
  .brand__dot { border-radius: 50%; background: var(--mark); flex: none; }
  .brand__name { font-weight: 600; color: var(--navy); letter-spacing: 1px; line-height: 1; }
  .brand--light .brand__name { color: var(--white); }

  .person {
    position: absolute; left: 0; right: 0; top: 172px;
    text-align: center; font-size: 13px; color: var(--ink);
  }
  .person__name { font-size: 18px; font-weight: 600; }
  .contact {
    position: absolute; left: 0; right: 0; top: 218px;
    text-align: center; font-size: 13.5px; color: var(--ink); line-height: 21px;
  }
  .contact b { font-style: italic; font-weight: 700; }
  .footer-band { position: absolute; left: 0; right: 0; bottom: 0; height: 32px; }
  .footer-band svg { position: absolute; inset: 0; }
  .footer-band span {
    position: absolute; top: 7px; font-size: 13px; color: var(--white);
  }
  .web {
    position: absolute; left: 0; right: 0;
    text-align: center; font-size: 16px; letter-spacing: 3px;
  }
  .web--dark { color: var(--muted); }
  .web--light { color: var(--white); }
</style>
</head>
<body>
  <div class="card-label" style="left:166px; top:34px;">Front</div>
  <div class="card-label" style="left:735px; top:34px;">Back - 1</div>
  <div class="card-label" style="left:166px; top:405px;">Back - 2</div>
  <div class="card-label" style="left:735px; top:405px;">Back - 3</div>

  <section class="card card--front">
    <div class="brand" style="left:132px; top:60px;">
      <span class="brand__dot" style="width:56px; height:56px;"></span>
      <span class="brand__name" style="font-size:40px;">VELUNDA</span>
    </div>
    <p class="person"><span class="person__name">Your Name,</span> Designation</p>
    <p class="contact">
      <b>p</b> : +12 345 67890 | <b>f</b> : +12 345 67890<br>
      #0000, Street Name, Area Name, Country Code
    </p>
    <div class="footer-band">
      <svg width="527" height="32" viewBox="0 0 527 32" aria-hidden="true">
        <rect width="527" height="32" fill="var(--navy)"/>
        <polygon points="0,0 232,0 250,32 0,32" fill="var(--sky)"/>
        <polygon points="232,0 240,0 258,32 250,32" fill="#d8d8d8"/>
      </svg>
      <span style="left:68px;">info@website.com</span>
      <span style="left:335px;">www.website.com</span>
    </div>
  </section>

  <section class="card card--white">
    <div class="brand" style="left:98px; top:86px;">
      <span class="brand__dot" style="width:72px; height:72px;"></span>
      <span class="brand__name" style="font-size:50px;">VELUNDA</span>
    </div>
    <p class="web web--dark" style="top:258px;">www.website.com</p>
  </section>

  <section class="card card--steel">
    <div class="brand" style="left:100px; top:98px;">
      <span class="brand__dot" style="width:66px; height:66px;"></span>
      <span class="brand__name" style="font-size:46px;">VELUNDA</span>
    </div>
    <p class="web web--light" style="top:262px;">www.website.com</p>
  </section>

  <section class="card card--navy">
    <span class="brand__dot" style="position:absolute; left:222px; top:42px; width:82px; height:82px;"></span>
    <p class="brand--light" style="position:absolute; left:0; right:0; top:178px; text-align:center;">
      <span class="brand__name" style="font-size:46px;">VELUNDA</span>
    </p>
    <p class="web web--light" style="top:262px;">www.website.com</p>
  </section>
</body>
</html>
```